Business Card for a mobile physiotherapy company

I need a layout for a business card for a mobile physiotherapy company.
Slogan is "Mobile Physiotherapy - Your Road To Recovery"
Phone number is 867-555-0142
Email VardenTherapy@postnest.ca (subject to change with website)
Website www.VardenTherapy.ca
My name and credentials: Luke Varden Luke Varden, BSc(kin), MPT, CAFCI, IMS
Information maybe included: Direct Billing, Services including Physiotherapy, IMS, acupuncture
Maybe include facebook and instagram logos
One side with the logo clean and sharp
Other side with details, try not to look too busy, keep everything concise

```html
<!DOCTYPE html>
<html lang="en">
<head>
<meta charset="utf-8">
<title>Varden Therapy – Business Card</title>
<link href="https://fonts.googleapis.com/css2?family=Lora:wght@400;700&display=swap" rel="stylesheet">
<style>
  :root {
    --navy: #2c4a76;
    --green: #1d5a48;
    --ink: #2f3f5c;
    --card: #f2f2f1;
    --backdrop: #b9b9b9;
  }
  * { box-sizing: border-box; margin: 0; padding: 0; }
  html, body { width: 1200px; height: 576px; overflow: hidden; }
  body {
    background: var(--backdrop);
    font-family: "Lora", Georgia, serif;
    color: var(--ink);
    position: relative;
  }
  .card {
    position: absolute;
    top: 139px;
    width: 482px;
    height: 291px;
    background: var(--card);
    border-radius: 12px;
    overflow: hidden;
  }
  .card::after {
    content: "";
    position: absolute;
    left: 0; right: 0; bottom: 0;
    height: 7px;
    background: linear-gradient(90deg, var(--green), var(--navy));
  }
  .card--front { left: 82px; }
  .card--back { left: 602px; }

  .brand-name {
    font-family: "Lora", Georgia, serif;
    font-weight: 700;
    color: var(--navy);
    text-transform: uppercase;
    letter-spacing: 0.12em;
    text-align: center;
    white-space: nowrap;
  }
  .card--front .brand-name {
    position: absolute;
    left: 0; right: 0;
    top: 112px;
    font-size: 34px;
  }
  .services {
    position: absolute;
    left: 0; right: 0;
    top: 259px;
    text-align: center;
    font-size: 12px;
    color: var(--ink);
    word-spacing: 1px;
  }
  .services .sep { margin: 0 5px; }

  .accent-dot {
    position: absolute;
    left: -14px; top: 57px;
    width: 22px; height: 42px;
    border-radius: 0 21px 21px 0;
    background: var(--green);
  }
  .holder-name {
    position: absolute;
    left: 22px; top: 48px;
    font-size: 20px;
    font-weight: 700;
    letter-spacing: 0.03em;
    color: var(--navy);
  }
  .credentials {
    position: absolute;
    left: 22px; top: 76px;
    font-size: 11px;
    color: var(--ink);
  }
  .card--back .brand-name {
    position: absolute;
    right: 28px; top: 88px;
    font-size: 20px;
    color: var(--green);
  }
  .social {
    position: absolute;
    left: 22px; top: 185px;
    display: flex; align-items: center; gap: 4px;
    font-size: 12.5px;
  }
  .social .dot {
    width: 19px; height: 19px; border-radius: 50%;
    background: var(--navy);
  }
  .social .dot + .dot { background: var(--green); }
  .social .label { margin-right: 3px; }
  .contact {
    position: absolute;
    left: 22px; top: 216px;
    list-style: none;
    font-size: 12.5px;
    line-height: 17px;
  }
  .contact li { display: flex; align-items: center; gap: 12px; }
  .contact svg { width: 12px; height: 12px; fill: var(--green); }
  .tagline {
    position: absolute;
    right: 32px; top: 233px;
    text-align: right;
    font-size: 12.5px;
    line-height: 17px;
  }
</style>
</head>
<body>
  <section class="card card--front" aria-label="Card front">
    <div class="brand-name">Varden Therapy</div>
    <p class="services">Direct Billing<span class="sep">|</span>Services Including Physiotherapy<span class="sep">|</span>IMS<span class="sep">|</span>Acupuncture</p>
  </section>

  <section class="card card--back" aria-label="Card back">
    <span class="accent-dot"></span>
    <h1 class="holder-name">LUKE VARDEN</h1>
    <p class="credentials">BSc(kin), MPT, CAFCI, IMS</p>
    <div class="brand-name">Varden Therapy</div>

    <div class="social">
      <span class="label">Follow us on:</span>
      <span class="dot"></span>
      <span class="dot"></span>
    </div>

    <ul class="contact">
      <li>
        <svg viewBox="0 0 24 24" aria-hidden="true"><path d="M6.6 10.8a15.1 15.1 0 0 0 6.6 6.6l2.2-2.2c.3-.3.7-.4 1-.2 1.1.4 2.3.6 3.6.6.6 0 1 .4 1 1V20c0 .6-.4 1-1 1A17 17 0 0 1 3 4c0-.6.4-1 1-1h3.5c.6 0 1 .4 1 1 0 1.3.2 2.5.6 3.6.1.3 0 .7-.2 1z"/></svg>
        <span>867-555-0142</span>
      </li>
      <li>
        <svg viewBox="0 0 24 24" aria-hidden="true"><path d="M2 5h20v14H2z M3.5 6.5 12 13l8.5-6.5" fill="none" stroke="#1d5a48" stroke-width="2.5"/></svg>
        <span>VardenTherapy@postnest.ca</span>
      </li>
      <li>
        <svg viewBox="0 0 24 24" aria-hidden="true"><circle cx="12" cy="12" r="9.5" fill="none" stroke="#1d5a48" stroke-width="2.2"/><path d="M2.5 12h19M12 2.5c3 3 3 16 0 19M12 2.5c-3 3-3 16 0 19" fill="none" stroke="#1d5a48" stroke-width="1.8"/></svg>
        <span>www.VardenTherapy.ca</span>
      </li>
    </ul>

    <p class="tagline">Mobile Physiotherapy<br>Your Road To Recovery</p>
  </section>
</body>
</html>
```